first fantastic look and impression

We are looking for a concept for letterhead, business card, emailfooter and template for invoices or offers for our company in the consultation business.
The dancer is a symbol who we are: it looks simple, but there is a lot of hard work and many years of training in this movement. The look is also what we want: elegant, modern, strong, with a touch of extravaganza
Target Market(s)
Hotelbusiness , Consulting
Font styles to use
Sans Serif
Other font styles liked:
- please give us a option we are open
Requirements
Must have
- We are not typical consultants but sparring partners and coaches for the hotel and that should also be expressed in the design. Maybe there is an icon that supports the whole thing. We are more modern and bolder than our industry colleagues.
we are modern, fresh, agile, fast
Nice to have
- a icon

```html
<!DOCTYPE html>
<html lang="en">
<head>
<meta charset="utf-8">
<title>Velmora Partners – Stationery</title>
<link rel="stylesheet" href="https://fonts.googleapis.com/css2?family=Montserrat:wght@400;500;600;700&display=swap">
<style>
  :root{
    --ink:#1c1e26;
    --paper:#ffffff;
    --stage:#efefef;
    --stage-alt:#e6e6e6;
    --row:#f1f2f4;
    --rule:#9a9ca3;
    --muted:#6c6e75;
    --accent:#c8142e;
  }
  *{box-sizing:border-box;margin:0;padding:0}
  html,body{width:1200px;height:3978px;overflow:hidden}
  body{font-family:'Montserrat',sans-serif;color:var(--ink);background:var(--stage);position:relative}

  .section{position:absolute;left:0;width:1200px}
  .section--sheets{top:0;height:800px;background:var(--stage)}
  .section--envelopes{height:795px;background:linear-gradient(160deg,#e9e9e9,#dedede)}

  .sheet{position:absolute;top:110px;width:410px;height:573px;background:var(--paper);box-shadow:0 6px 18px rgba(0,0,0,.12);padding:0}
  .sheet--invoice{left:165px}
  .sheet--letter{left:613px;width:407px}

  .brand{position:absolute;left:26px;top:44px;font-weight:600;font-size:13px;letter-spacing:.06em;text-transform:uppercase;color:var(--ink)}
  .contact{position:absolute;right:26px;top:36px;list-style:none;font-size:7.5px;line-height:11.5px}
  .contact li{display:flex;align-items:center;gap:4px}
  .contact svg{width:8px;height:8px}

  .invoice-title{position:absolute;left:26px;top:118px;font-size:11px;font-weight:700}
  .invoice-date{position:absolute;left:300px;top:122px;font-size:6px;color:#3d7a55}
  .field{position:absolute;left:26px;font-size:6px;display:flex;gap:4px;align-items:flex-end}
  .field span.line{display:block;border-bottom:1px solid var(--rule);height:8px}

  .items{position:absolute;left:26px;top:196px;width:358px;border-collapse:collapse;font-size:7px}
  .items th{background:var(--ink);color:#fff;font-weight:600;height:20px;letter-spacing:.04em}
  .items td{height:15px;border-left:1px solid var(--rule);border-right:1px solid var(--rule)}
  .items tr:nth-child(odd) td{background:var(--row)}
  .items tbody tr:last-child td{border-bottom:1px solid var(--rule)}

  .totals{position:absolute;left:260px;top:396px;width:124px;border-collapse:collapse;font-size:6px}
  .totals td{border:1px solid var(--rule);height:20px;padding-left:5px;font-weight:600}
  .totals td:last-child{width:62px}

  .payments{position:absolute;left:26px;top:408px;display:flex;gap:9px;font-size:5.5px}
  .payments span{display:flex;align-items:center;gap:2px}
  .payments i{display:inline-block;width:7px;height:7px;border:1px solid var(--muted)}
  .terms{position:absolute;left:26px;top:436px;font-size:6px;line-height:8px;color:var(--muted)}

  .letter-body{position:absolute;left:36px;top:148px;width:336px;font-size:6.4px;line-height:9.6px;color:var(--muted)}
  .letter-body p{margin-bottom:10px}
  .signature{display:block;width:48px;height:34px;background:linear-gradient(135deg,#eceef1,#dcdde1);border-radius:3px}

  .envelope{position:absolute;width:640px;height:300px;background:var(--paper);box-shadow:0 8px 22px rgba(0,0,0,.1)}
  .envelope--back{left:420px;top:70px}
  .envelope--front{left:160px;top:400px}
  .flap{position:absolute;left:0;top:0;width:100%;height:96px;border-bottom:1px solid #dcdcdc;background:#f6f6f6}
  .flap--dark{background:var(--ink);border-bottom:none}
  .seal{position:absolute;left:298px;top:74px;width:44px;height:44px;border-radius:50%}
  .seal--dark{background:var(--ink)}
  .seal--light{background:#f4f4f4}
  .seal--outline{border:1px solid #8a8c92;background:transparent}
  .seal--outline-dark{border:1px solid #9a9ca3;background:var(--ink)}
  .front-brand{position:absolute;left:34px;top:34px;font-weight:600;font-size:15px;letter-spacing:.06em;text-transform:uppercase}
  .front-address{position:absolute;left:34px;top:56px;font-size:8px;color:var(--muted)}

  .variant-number{position:absolute;left:975px;top:500px;font-size:130px;font-weight:400;color:var(--accent);line-height:1}
</style>
</head>
<body>

<section class="section section--sheets">
  <article class="sheet sheet--invoice">
    <div class="brand">Velmora Partners</div>
    <ul class="contact">
      <li><svg viewBox="0 0 8 8"><circle cx="4" cy="4" r="4" fill="#1c1e26"/><circle cx="4" cy="3.4" r="1.2" fill="#fff"/></svg>4120 Lindhof / Weidenweg 12</li>
      <li><svg viewBox="0 0 8 8"><circle cx="4" cy="4" r="4" fill="#1c1e26"/><rect x="3" y="2" width="2" height="4" rx=".6" fill="#fff"/></svg>+43 5500 41270</li>
      <li><svg viewBox="0 0 8 8"><circle cx="4" cy="4" r="4" fill="#1c1e26"/><rect x="2" y="2.8" width="4" height="2.6" fill="#fff"/></svg>ma@velmorapartners.com</li>
      <li><svg viewBox="0 0 8 8"><circle cx="4" cy="4" r="4" fill="#1c1e26"/><circle cx="4" cy="4" r="2" fill="none" stroke="#fff" stroke-width=".8"/></svg>velmorapartners.com</li>
    </ul>
    <h1 class="invoice-title">INVOICE # :</h1>
    <div class="invoice-date">DATE :</div>
    <div class="field" style="top:138px"><span>Customer :</span><span class="line" style="width:312px"></span></div>
    <div class="field" style="top:155px"><span>Address :</span><span class="line" style="width:316px"></span></div>
    <div class="field" style="top:172px"><span>Phone :</span><span class="line" style="width:150px"></span><span>Fax :</span><span class="line" style="width:140px"></span></div>

    <table class="items">
      <thead><tr><th style="width:48px">QTY</th><th style="width:186px">DESCRIPTION</th><th style="width:62px">PRICE</th><th style="width:62px">AMOUNT</th></tr></thead>
      <tbody>
        <tr><td></td><td></td><td></td><td></td></tr><tr><td></td><td></td><td></td><td></td></tr>
        <tr><td></td><td></td><td></td><td></td></tr><tr><td></td><td></td><td></td><td></td></tr>
        <tr><td></td><td></td><td></td><td></td></tr><tr><td></td><td></td><td></td><td></td></tr>
        <tr><td></td><td></td><td></td><td></td></tr><tr><td></td><td></td><td></td><td></td></tr>
        <tr><td></td><td></td><td></td><td></td></tr><tr><td></td><td></td><td></td><td></td></tr>
        <tr><td></td><td></td><td></td><td></td></tr>
      </tbody>
    </table>

    <table class="totals">
      <tr><td>SUB TOTAL</td><td></td></tr>
      <tr><td>GST #</td><td></td></tr>
      <tr><td>SUBTOTAL</td><td></td></tr>
    </table>

    <div class="payments">
      <span><i></i>VISA</span><span><i></i>MC</span><span><i></i>DEBIT</span><span><i></i>CASH</span><span><i></i>CHEQUE</span>
    </div>
    <p class="terms">Signature Indicates<br>Acceptance of Price and term</p>
  </article>

  <article class="sheet sheet--letter">
    <div class="brand">Velmora Partners</div>
    <ul class="contact">
      <li><svg viewBox="0 0 8 8"><circle cx="4" cy="4" r="4" fill="#1c1e26"/><circle cx="4" cy="3.4" r="1.2" fill="#fff"/></svg>4120 Lindhof / Weidenweg 12</li>
      <li><svg viewBox="0 0 8 8"><circle cx="4" cy="4" r="4" fill="#1c1e26"/><rect x="3" y="2" width="2" height="4" rx=".6" fill="#fff"/></svg>+43 5500 41270</li>
      <li><svg viewBox="0 0 8 8"><circle cx="4" cy="4" r="4" fill="#1c1e26"/><rect x="2" y="2.8" width="4" height="2.6" fill="#fff"/></svg>ma@velmorapartners.com</li>
      <li><svg viewBox="0 0 8 8"><circle cx="4" cy="4" r="4" fill="#1c1e26"/><circle cx="4" cy="4" r="2" fill="none" stroke="#fff" stroke-width=".8"/></svg>velmorapartners.com</li>
    </ul>
    <div class="letter-body">
      <p>Dear customer,</p>
      <p>Thank you for the trust you place in our team. This letter outlines the next steps of our joint work, the timeline we agreed on and the people who will guide each phase of the project with you.</p>
      <p>During the first weeks we will visit your house, talk with your staff and review the figures that matter most. From these findings we will shape clear goals that everyone can follow and measure.</p>
      <p>We work as sparring partners, not as distant advisers. Expect honest questions, quick feedback and practical tools your managers can use the very next day at the front desk and behind it.</p>
      <p>Please contact us at any time if you have questions. We look forward to a strong season together.</p>
      <p>Yours Sincerely,</p>
      <span class="signature" role="img" aria-label="Handwritten signature"></span>
    </div>
  </article>
</section>

<section class="section section--envelopes" style="top:800px">
  <div class="envelope envelope--back"><div class="flap"></div><div class="seal seal--dark"></div></div>
  <div class="envelope envelope--front"><div class="front-brand">Velmora Partners</div><div class="front-address">4120 Lindhof / Weidenweg 12</div></div>
  <div class="variant-number">1</div>
</section>

<section class="section section--envelopes" style="top:1595px">
  <div class="envelope envelope--back"><div class="flap flap--dark"></div><div class="seal seal--light"></div></div>
  <div class="envelope envelope--front"><div class="front-brand">Velmora Partners</div><div class="front-address">4120 Lindhof / Weidenweg 12</div></div>
  <div class="variant-number">2</div>
</section>

<section class="section section--envelopes" style="top:2390px">
  <div class="envelope envelope--back"><div class="flap"></div><div class="seal seal--outline"></div></div>
  <div class="envelope envelope--front"><div class="front-brand">Velmora Partners</div><div class="front-address">4120 Lindhof / Weidenweg 12</div></div>
  <div class="variant-number">3</div>
</section>

<section class="section section--envelopes" style="top:3185px;height:793px">
  <div class="envelope envelope--back"><div class="flap flap--dark"></div><div class="seal seal--outline-dark"></div></div>
  <div class="envelope envelope--front"><div class="front-brand">Velmora Partners</div><div class="front-address">4120 Lindhof / Weidenweg 12</div></div>
  <div class="variant-number">4</div>
</section>

</body>
</html>
```